Cafe menu flyer design

I need if possible A4 double sided menus. Two exemplars: first will contain breakfast menu on one side & refreshments menu on the other side, second exemplar will contain lunch menu on one side & refreshments menu on the other side. We do not need a description of the cafe or any history on these flyers, but design should reflect our surroundings and activities this area. We are located in main ski resort in UK-Cairngorm Mountains, right on the main ski road. The slopes are only 2 miles away from us. We are also very popular with wild life enthusiasts. Continues in design brief!

Cafe

```html
<!DOCTYPE html>
<html lang="en">
<head>
<meta charset="utf-8">
<title>Fiona's @ Pinewood Cafe – Lunch Menu</title>
<link rel="stylesheet" href="https://fonts.googleapis.com/css2?family=Lato:wght@400;700&family=Tinos:ital,wght@1,400;1,700&display=swap">
<style>
  :root {
    --canvas-bg: #e9eeee;
    --navy: #1f2f7a;
    --ink: #1b1b1b;
    --price-blue: #2b3f8f;
    --snow-top: #b9cce0;
    --snow-mid: #e4ecf4;
    --snow-low: #f6f8fb;
    --band: #a9b3d4;
    --squirrel: #e07b22;
    --lemon: #e8c23a;
  }
  * { box-sizing: border-box; margin: 0; padding: 0; }
  html, body { width: 1200px; height: 960px; overflow: hidden; }
  body { background: var(--canvas-bg); font-family: "Lato", Arial, sans-serif; color: var(--ink); position: relative; }

  .menu-sheet {
    position: absolute; left: 282px; top: 30px; width: 636px; height: 900px;
    background: var(--snow-low); overflow: hidden;
    box-shadow: 0 6px 24px rgba(0,0,0,.12);
  }
  .mountain-scene {
    position: absolute; inset: 0;
    background:
      radial-gradient(ellipse 40% 30% at 28% 52%, rgba(90,110,140,.28), transparent 70%),
      linear-gradient(180deg, var(--snow-top) 0%, var(--snow-mid) 35%, var(--snow-low) 70%, #fff 100%);
  }
  .cafe-name {
    position: absolute; top: 46px; left: 0; right: 0; text-align: center;
    font-weight: 700; font-size: 27px; color: var(--navy);
  }
  .menu-column { position: absolute; top: 108px; }
  .menu-column--lunch { left: 15px; width: 276px; }
  .menu-column--drinks { left: 326px; width: 292px; }
  .column-divider { position: absolute; left: 315px; top: 108px; width: 2px; height: 724px; background: var(--navy); }

  .column-heading {
    font-weight: 700; font-size: 16px; color: var(--navy);
    padding-bottom: 6px; border-bottom: 2px solid var(--navy); margin-bottom: 16px;
  }
  .menu-item { display: flex; justify-content: space-between; align-items: flex-end; gap: 6px; font-size: 11px; line-height: 13.5px; margin-bottom: 11.5px; }
  .menu-item .price { color: var(--price-blue); white-space: nowrap; }
  .menu-item--stack { display: block; }
  .item-options { font-size: 11px; line-height: 13.5px; margin-bottom: 11.5px; }
  .item-options em { font-family: "Tinos", serif; font-style: italic; color: var(--price-blue); }
  .price-inline { color: var(--price-blue); }

  .menu-note { font-family: "Tinos", "Times New Roman", serif; font-style: italic; font-weight: 700; color: var(--navy); font-size: 11.5px; line-height: 13.5px; }

  .enjoy-band {
    position: absolute; left: 0; top: 736px; width: 315px; height: 74px;
    background: var(--band); color: var(--navy);
    font-size: 16px; padding: 28px 0 0 15px; letter-spacing: .5px;
  }
  .squirrel-art { position: absolute; left: 200px; top: 715px; width: 112px; height: 118px; }
  .lemon-art { position: absolute; left: 454px; top: 846px; width: 168px; height: 56px; }

  .footer-rule { position: absolute; left: 0; right: 0; top: 832px; height: 2px; background: var(--navy); }
  .footer-contact { position: absolute; top: 840px; left: 0; right: 0; text-align: center; font-family: "Tinos", serif; font-style: italic; font-weight: 700; font-size: 11px; line-height: 15px; color: var(--navy); }
</style>
</head>
<body>
  <article class="menu-sheet">
    <div class="mountain-scene" role="img" aria-label="Photograph of a skier descending a snowy mountain slope under a pale blue sky"></div>

    <h1 class="cafe-name">Fiona's @ Pinewood Cafe</h1>

    <section class="menu-column menu-column--lunch">
      <h2 class="column-heading">Lunch menu 12-4pm</h2>
      <div class="menu-item"><span>Soup of the day, served with brown roll &amp; butter</span><span class="price">£3.75</span></div>
      <div class="item-options">Freshly made toasties: one filling <span class="price-inline">£3.20</span>, two fillings <span class="price-inline">£4.20</span></div>
      <div class="item-options">Sundried tomato,pesto and Mozzarella cheese</div>
      <div class="item-options">Mozzarella and salami<br>Cheese and ham<br>Cheese and onion<br>Cheese and tomato<br><em>(Paninis with fillings as above coming soon! One filling £4.20, Two filling £5.20</em></div>
      <div class="menu-item"><span>Local butchers beef burger meal,served with chips and salad</span><span class="price">£7.95</span></div>
      <div class="menu-item"><span>Home made chicken fillet burger meal, served with chips and salad</span><span class="price">£7.95</span></div>
      <div class="menu-item"><span>Burger in a bun( on its own)</span><span class="price">£4.20</span></div>
      <div class="menu-item"><span>Pies assorted</span><span class="price">£2.50</span></div>
      <div class="menu-item"><span>Pie with beans</span><span class="price">£3.50</span></div>
      <div class="menu-item"><span>Pie with chips</span><span class="price">£5.00</span></div>
      <div class="menu-item"><span>Pie with beans and chips</span><span class="price">£6.00</span></div>
      <div class="menu-item"><span>Basket of chips</span><span class="price">£3.50</span></div>
      <div class="menu-item"><span>Chip butty</span><span class="price">£2.00</span></div>
      <div class="menu-item"><span>Chips &amp; beans</span><span class="price">£4.50</span></div>
      <div class="menu-item"><span>Chips &amp; cheese</span><span class="price">£4.50</span></div>
      <div class="menu-item"><span>Rolls with assorted cold fillings</span><span class="price">£2.20 - £3.20</span></div>
      <p class="menu-note">Gluten free bread and cakes available- ask staff!<br>At the hight of the season evening meals available.<br>Ask staff for more information.</p>
    </section>

    <div class="column-divider"></div>

    <section class="menu-column menu-column--drinks">
      <h2 class="column-heading">Refreshments</h2>
      <div class="menu-item"><span>Tea</span><span class="price">£1.50</span></div>
      <div class="menu-item"><span>Filter Coffee, decaf coffee, plain hot chocolate</span><span class="price">£2.00</span></div>
      <div class="menu-item"><span>Selection of herbal teas</span><span class="price">£2.00</span></div>
      <div class="menu-item"><span>Specialty strawberry, raspberry, apple &amp; mint tea( black tea with your choice of syrup)</span><span class="price">£2.50</span></div>
      <div class="menu-item"><span>Assorted premium "Leaf House" teas</span><span class="price">£2.50</span></div>
      <div class="menu-item"><span>Hot chocolate with cream</span><span class="price">£2.20</span></div>
      <div class="menu-item"><span>Hot chocolate with marsh mallows</span><span class="price">£2.20</span></div>
      <div class="menu-item"><span>Hot chocolate with cream &amp; marsh mallows</span><span class="price">£2.20</span></div>
      <div class="menu-item"><span>Hot chocolate with brandy</span><span class="price">£3.50</span></div>
      <div class="menu-item"><span>Hot chocolate with brandy,<br>marsh mallows &amp; cream</span><span class="price">£4.50</span></div>
      <div class="menu-item"><span>Cafe Latte/Cappucino</span><span class="price">£2.50</span></div>
      <div class="menu-item"><span>Squirrel Latte</span><span class="price">£3.50</span></div>
      <div class="menu-item"><span>Chocolate Latte</span><span class="price">£3.50</span></div>
      <div class="menu-item"><span>Cinnamon Latte</span><span class="price">£3.50</span></div>
      <div class="menu-item"><span>Caramel Latte</span><span class="price">£3.50</span></div>
      <div class="menu-item"><span>Butterscotch Latte</span><span class="price">£3.50</span></div>
      <div class="menu-item"><span>Gingerbread Latte</span><span class="price">£3.50</span></div>
      <div class="menu-item"><span>Mocha</span><span class="price">£3.50</span></div>
      <div class="menu-item"><span>Glass of milk</span><span class="price">£1.20</span></div>
      <div class="menu-item"><span>Milkshakes</span><span class="price">£2.00</span></div>
      <div class="menu-item"><span>Still or Sparkling water</span><span class="price">£1.80</span></div>
      <div class="menu-item"><span>Cans of juice</span><span class="price">£1.60</span></div>
      <div class="menu-item"><span>Cartons of juice</span><span class="price">£1.30</span></div>
      <p class="menu-note" style="margin-bottom:10px">We use semi skimmed milk only</p>
      <p class="menu-note">At the hight of the season evening meals available. Ask staff for more information.</p>
    </section>

    <div class="enjoy-band">ENJOY YOUR MEAL !!!</div>

    <svg class="squirrel-art" role="img" aria-label="Illustration of a red squirrel" viewBox="0 0 112 118">
      <ellipse cx="56" cy="62" rx="46" ry="52" fill="var(--squirrel)" opacity=".85"/>
    </svg>

    <div class="footer-rule"></div>
    <p class="footer-contact">Fionas @ Pinewood Cafe, Pinewood, Strathbeg, PH99 4ZZ. Tel:01234567890<br>Like us on social media</p>

    <svg class="lemon-art" role="img" aria-label="Illustration of yellow fruit" viewBox="0 0 168 56">
      <ellipse cx="84" cy="30" rx="78" ry="24" fill="var(--lemon)"/>
    </svg>
  </article>
</body>
</html>
```